Veterinary Pylon

My veterinary clinic is not clearly visible from the street and I want to place a Pylon next to my driveway. I want a modern, elegant straight Design, the Photo shows the sheduled place. One can see the clinic on our Homepage: www.tailbright-vethaus.at
The last pictures are examples for pylones I like

Target Market(s)

the passing cars often miss my entry...I want to show where to turn left

Colors
3276b5
33a6d7
00a990

Requirements
Must have
• High value, simple elegance, size: 250cm (high) x 100cm (width)
Nice to have
• Our Logo, arrow(?)

A special Text is not necessary but this will be an option:

Biegen sie hier ab und wir biegen es wieder hin!
Should not have
• Too much Color, the colors I have chosen are the possible colors but it‘s not necessary to use them.

```html
<!DOCTYPE html>
<html lang="de">
<head>
<meta charset="utf-8">
<title>Tailbright Vethaus – Pylon</title>
<link href="https://fonts.googleapis.com/css2?family=Montserrat:wght@400;500;600;700;800&display=swap" rel="stylesheet">
<style>
  :root {
    --navy: #284a8c;
    --sky: #42badf;
    --white: #ffffff;
    --backdrop: #eef1f4;
  }
  html, body {
    margin: 0;
    padding: 0;
    width: 818px;
    height: 1200px;
    overflow: hidden;
    background: var(--backdrop);
    font-family: "Montserrat", sans-serif;
  }
  .pylon {
    position: absolute;
    left: 179px;
    top: 25px;
    width: 460px;
    height: 1150px;
    background: var(--white);
    overflow: hidden;
  }
  .pylon__band {
    position: absolute;
    left: 0;
    top: 342px;
    width: 100%;
    bottom: 0;
    background: var(--sky);
  }
  .brand {
    position: absolute;
    left: 0;
    top: 90px;
    width: 100%;
    display: flex;
    align-items: center;
    justify-content: center;
    gap: 14px;
  }
  .brand__dot {
    width: 46px;
    height: 46px;
    border-radius: 50%;
    background: var(--sky);
  }
  .brand__name {
    font-weight: 800;
    font-size: 31px;
    color: var(--navy);
    letter-spacing: 0.5px;
  }
  .info-panel {
    position: absolute;
    left: 80px;
    top: 224px;
    width: 380px;
    height: 676px;
    background: var(--navy);
  }
  .headline {
    position: absolute;
    left: 53px;
    top: 48px;
    margin: 0;
    font-weight: 700;
    font-size: 44px;
    line-height: 56px;
    color: var(--white);
    white-space: nowrap;
  }
  .hours {
    position: absolute;
    left: 52px;
    top: 339px;
    margin: 0;
    padding: 0;
    list-style: none;
  }
  .hours__group {
    border-left: 2px solid var(--white);
    padding-left: 9px;
    margin-bottom: 21px;
    height: 69px;
  }
  .hours__day {
    display: block;
    font-weight: 600;
    font-size: 18px;
    line-height: 22px;
    color: var(--sky);
    text-transform: uppercase;
    white-space: nowrap;
  }
  .hours__time {
    display: block;
    font-weight: 400;
    font-size: 19px;
    line-height: 23.5px;
    color: var(--white);
    white-space: nowrap;
  }
  .web-box {
    position: absolute;
    left: 80px;
    top: 900px;
    width: 380px;
    height: 100px;
    background: var(--white);
    display: flex;
    align-items: center;
    justify-content: center;
  }
  .web-box__url {
    font-weight: 500;
    font-size: 21px;
    color: var(--navy);
    letter-spacing: 0.2px;
    white-space: nowrap;
  }
  .turn-arrow {
    position: absolute;
    left: 170px;
    top: 1040px;
    width: 200px;
    height: 90px;
  }
</style>
</head>
<body>
  <main class="pylon">
    <div class="pylon__band"></div>

    <header class="brand">
      <span class="brand__dot"></span>
      <span class="brand__name">Tailbright Vethaus</span>
    </header>

    <section class="info-panel">
      <h1 class="headline">Biegen<br>Sie ein,<br>dann biegen<br>wir es hin!</h1>

      <ul class="hours">
        <li class="hours__group">
          <span class="hours__day">Monday - Friday</span>
          <span class="hours__time">08:00 - 12:00</span>
          <span class="hours__time">14:00 - 19:00</span>
        </li>
        <li class="hours__group">
          <span class="hours__day">Saturday</span>
          <span class="hours__time">08:00 - 12:00</span>
          <span class="hours__time">17:00 - 18:00</span>
        </li>
        <li class="hours__group">
          <span class="hours__day">Sunday</span>
          <span class="hours__time">10:00 am - 11:00 am</span>
          <span class="hours__time">17:00 - 18:00</span>
        </li>
      </ul>
    </section>

    <footer class="web-box">
      <span class="web-box__url">www.tailbright-vethaus.at</span>
    </footer>

    <svg class="turn-arrow" viewBox="0 0 200 90" role="img" aria-label="Pfeil nach links: hier abbiegen">
      <polygon points="0,45 50,0 50,28 200,28 200,62 50,62 50,90" fill="#ffffff"/>
    </svg>
  </main>
</body>
</html>
```